Business cards for veterinary clinic

Hi, We are looking for business cards to be designed for our other veterinary clinic. We were very happy with the design done for our other clinic a few months ago. We already have a logo for use which I will attach (please use the image not the text around.
We need a couple of different cards (same design with different names on them) produced

Industry/Entity Type

Veterinary

Contact Information for Business Card

Bellwood Creek Vet Clinic
47 Orchard Rd
Kangaroo Flat
VIC 3555
03) 5182 6390
clinic@bellwoodcreekvetclinic.com.au

Font styles to use
Sans Serif

Colors
0455a3
0592cd

Requirements
Must have
• Three different names
• 1. Generic (no name) with email clinic@bellwoodcreekvetclinic.com.au
• 2. Hollis Varne -Director with email hollis@bellwoodcreekvetclinic.com.au
• 3. Dorian Pike - Vet Director with email hollis@bellwoodcreekvetclinic.com.au

```html
<!DOCTYPE html>
<html lang="en">
<head>
<meta charset="utf-8">
<title>Bellwood Creek Vet Clinic – Business Cards</title>
<link rel="stylesheet" href="https://fonts.googleapis.com/css2?family=Jost:wght@400;500&display=swap">
<style>
  :root {
    --backdrop: #1d2b3b;
    --card: #f7f8f8;
    --navy: #1f4c9c;
    --sky: #7ccfdf;
    --rule: #6fcbe0;
    --mark: #8fd3e4;
    --back-top: #eef0f3;
    --back-tint: #d6dce7;
    --back-arc: #c9d2de;
  }
  * { margin: 0; padding: 0; box-sizing: border-box; }
  html, body {
    width: 1200px; height: 1000px; overflow: hidden;
    background: var(--backdrop);
    font-family: "Jost", sans-serif;
  }
  .cards { position: relative; width: 1200px; height: 1000px; }
  .card {
    position: absolute; top: 150px;
    width: 420px; height: 700px;
    background: var(--card);
    border-radius: 4px;
    box-shadow: 0 18px 40px rgba(0,0,0,0.45);
    overflow: hidden;
  }
  .card--front { left: 130px; padding: 40px 40px 0; text-align: center; }
  .card--back { left: 650px; background: linear-gradient(180deg, var(--back-top) 0%, var(--card) 100%); }

  .brand-mark {
    display: block; width: 140px; height: 140px; margin: 0 auto 16px;
    border-radius: 50%;
    background: var(--mark);
  }
  .clinic-name {
    color: var(--sky); font-weight: 400; font-size: 32px;
    line-height: 1.05; letter-spacing: 1px; text-transform: uppercase;
  }
  .rule { display: block; height: 2px; background: var(--rule); margin: 24px 0; border: 0; }
  .person-name {
    color: var(--navy); font-weight: 400; font-size: 38px;
    letter-spacing: 1px; text-transform: uppercase; line-height: 1;
  }
  .person-role {
    color: var(--sky); font-size: 15px; letter-spacing: 1.5px;
    text-transform: uppercase; margin-top: 4px;
  }
  .phone {
    color: var(--navy); font-size: 60px; font-weight: 400;
    letter-spacing: 2px; line-height: 1;
  }
  .contact {
    color: var(--navy); font-size: 14px; letter-spacing: 1px;
    text-transform: uppercase; line-height: 1.55; font-style: normal;
  }
  .back-arc { position: absolute; left: 0; top: 0; width: 420px; height: 700px; }
  .back-art {
    position: absolute; left: 0; right: 0; bottom: 0; height: 430px;
    background: linear-gradient(180deg, rgba(214,220,231,0) 0%, var(--back-tint) 55%, #e4e8ef 100%);
  }
</style>
</head>
<body>
  <main class="cards">
    <section class="card card--front" aria-label="Business card front">
      <span class="brand-mark" aria-hidden="true"></span>
      <h1 class="clinic-name">Bellwood Creek<br>Vet Clinic</h1>
      <hr class="rule">
      <h2 class="person-name">Hollis Varne</h2>
      <p class="person-role">Director</p>
      <hr class="rule">
      <p class="phone">5182 6390</p>
      <hr class="rule">
      <address class="contact">
        47 Orchard Rd Bellwood<br>
        Creek VIC 3621 03<br>
        hollis@bellwoodcreekvetclinic.com.au
      </address>
      <hr class="rule">
    </section>

    <section class="card card--back" aria-label="Business card back">
      <div class="back-art" role="img" aria-label="Faint pale-blue silhouettes of a horse, cow, dog and cat"></div>
      <svg class="back-arc" viewBox="0 0 420 700" aria-hidden="true">
        <path d="M -20 330 Q 210 250 440 330" fill="none" stroke="var(--back-arc)" stroke-width="5"/>
      </svg>
    </section>
  </main>
</body>
</html>
```